Brookvale Estates LLC stationary for a real estate property management company.

Create stationary (letterhead, envelopes, business cards) using Brookvale Estates LLC logo as primary creative element. Stationary design needs to be horizontal, leaving as much space as possible for correspondence copy. See attached Creative Brief and past stationary files for details.

Target Market(s)

Prospective apartment residents and current residents, vendors, and government agencies.

Industry/Entity Type

Property Management

Contact Information for Business Card

Business card employee title: Property Manager. Should include address, phone, fax, email, website, slogan, and Brookvale Estates logo.

Font styles to use
Sans Serif

Colors
0592cd
000000

Requirements
Must have
• Tone should be conservative, institutional, business (i.e. banking, finance, real estate). Must include: address, phone, fax, website, and slogan (see attached Creative Brief). Should be a horizontal design, leaving as much room as possible for letter correspondence copy.
Nice to have
• Please use an Arial or Helvetica style font.
Should not have
• Letterhead layout should leave as much room as possible for copy.

```html
<!DOCTYPE html>
<html lang="en">
<head>
<meta charset="utf-8">
<title>Brookvale Estates LLC – Business Card</title>
<link href="https://fonts.googleapis.com/css2?family=Arimo:wght@400;700&display=swap" rel="stylesheet">
<style>
  :root {
    --stage: #2b2b2b;
    --brand-blue: #0592cd;
    --blue-light: #18bdee;
    --blue-deep: #0b65a6;
    --paper: #f6f6f6;
    --ink-white: #ffffff;
  }
  * { margin: 0; padding: 0; box-sizing: border-box; }
  html, body {
    width: 1200px; height: 960px; overflow: hidden;
    background: var(--stage);
    font-family: "Arimo", Arial, Helvetica, sans-serif;
  }
  .canvas { position: relative; width: 1200px; height: 960px; }
  .card {
    position: absolute; width: 600px; height: 342px;
  }
  .card-front {
    left: 302px; top: 129px;
    background: linear-gradient(135deg, var(--blue-light) 0%, var(--brand-blue) 30%, var(--blue-deep) 70%, var(--blue-deep) 100%);
    color: var(--ink-white);
    text-align: center;
  }
  .card-back {
    left: 299px; top: 489px;
    background: var(--paper);
    display: flex; align-items: center; justify-content: center; gap: 18px;
  }
  .brand-name-front {
    position: absolute; left: 0; right: 0; top: 100px;
    font-size: 26px; font-weight: 700; letter-spacing: 0.5px;
  }
  .person-name {
    position: absolute; left: 0; right: 0; top: 181px;
    font-size: 20px; font-weight: 700; letter-spacing: 0.2px;
  }
  .person-title {
    position: absolute; left: 0; right: 0; top: 204px;
    font-size: 15px; font-weight: 400;
  }
  .contact {
    position: absolute; left: 0; right: 0; top: 233px;
    font-size: 14px; line-height: 18px;
  }
  .contact b { font-weight: 700; }
  .brand-dot {
    width: 58px; height: 58px; border-radius: 50%;
    background: var(--brand-blue);
  }
  .brand-name-back {
    font-size: 40px; font-weight: 700; color: var(--brand-blue);
    letter-spacing: 0.3px;
  }
</style>
</head>
<body>
<main class="canvas">
  <section class="card card-front">
    <div class="brand-name-front">Brookvale Estates</div>
    <div class="person-name">DANA WHITFIELD</div>
    <div class="person-title">Property Manager</div>
    <div class="contact">
      <div><b>Phone</b>: 555-214-7730 <b>Fax</b>: 555-214-7731</div>
      <div>dana@brookvaleestates.us | www.brookvaleestates.us</div>
      <div>1820 Harbor Ridge Drive #B210, Lakemont, CA 90000</div>
    </div>
  </section>
  <section class="card card-back">
    <div class="brand-dot"></div>
    <div class="brand-name-back">Brookvale Estates LLC</div>
  </section>
</main>
</body>
</html>
```